QuillVane needs a dashboard page designed

Redesign the dashboard shown in the provided images.

There are two images:
- dashboard.png
- dashboard-expanded.png

NOTE: The vocabulary navigation on the left will be a very long list of words 100s, so keep that in mind when you're designing both the vocab navigation and the expanded vocab popup.

In the dashboard.png picture, there needs to be a progress chart showing the word progress like the following: review 1(show it as completed) -> review 2(show the user they are here) -> review 3(unvisited) -> review 4(unvisited)

The do-not-design-this-page.png image is for your reference only. It is not to be designed. Use it to understand the overall look and feel of the website to help you create the best dashboard page possible.
Updates

Need extra days to review

Industry/Entity Type

Education English learning

Number of Pages Required

1 page

Requirements
Must have
• The main navigation and main header cannot change between pages. See the do-not-design page for the main navigateion and header.
Should not have
• Do not add a person profile. We will not have images of our users. Keep the icons in the main navigation as they are.

```html
<!DOCTYPE html>
<html lang="en">
<head>
<meta charset="utf-8">
<title>QuillVane Dashboard</title>
<link rel="stylesheet" href="https://fonts.googleapis.com/css2?family=Roboto:wght@400;500;700&family=Rubik:wght@500;600;700&display=swap">
<style>
:root{
  --stage:#c2c2c2;
  --header:#f4f4f4;
  --side:#2b333d;
  --footer:#4f565f;
  --blue:#2d64b5;
  --ink:#2b2f33;
  --muted:#9aa0a6;
  --line:#d8dbdf;
  --white:#ffffff;
}
*{box-sizing:border-box;margin:0;padding:0}
html,body{width:1200px;height:711px;overflow:hidden}
body{background:var(--stage);position:relative;font-family:"Roboto",Arial,sans-serif;color:var(--ink)}
.screen{position:absolute;top:46px;width:1090px;height:1292px;transform:scale(.4794);transform-origin:0 0;background:var(--white);box-shadow:0 8px 30px rgba(0,0,0,.25);overflow:hidden}
.screen--main{left:55px}
.screen--expanded{left:623px}
.abs{position:absolute}

.app-header{left:0;top:0;width:1090px;height:96px;background:var(--header)}
.brand{left:36px;top:30px;font-family:"Rubik",sans-serif;font-weight:700;font-size:29px;letter-spacing:.5px;color:var(--ink)}
.search{left:407px;top:30px;width:406px;height:36px;border:1px solid #cfd3d7;border-radius:4px;background:#fff;font-size:11px;color:#333;padding:10px 0 0 30px}
.search svg{position:absolute;left:15px;top:12px}
.hdr-icon{top:40px}
.user{left:907px;top:40px;font-size:13px;font-weight:500;letter-spacing:.2px}
.avatar{left:1010px;top:26px;width:44px;height:44px;border-radius:50%;background:linear-gradient(135deg,#6b7480,#2c333b)}
.online{left:1043px;top:59px;width:10px;height:10px;border-radius:50%;background:#2fb44a;border:2px solid #fff}

.sidebar{left:0;top:96px;width:363px;height:1116px;background:var(--side)}
.select{height:40px;border:1.5px solid #fff;border-radius:5px;color:#fff;font-size:11px;font-weight:500;padding:13px 0 0 15px}
.select::after{content:"";position:absolute;right:10px;top:17px;border:5px solid transparent;border-top:6px solid #fff}
.expand-btn{left:189px;top:134px;width:145px;height:40px;background:var(--blue);border-radius:5px;color:#fff;font-size:13px;font-weight:500;text-align:center;line-height:40px}
.tree{left:36px;top:181px;width:298px;height:382px;background:#fff;border-radius:5px}
.tree-item{font-size:10px;font-weight:500;text-transform:uppercase;white-space:nowrap}
.tree-item::before{content:"";position:absolute;left:-14px;top:2px;border:4px solid transparent;border-left:5px solid currentColor}
.tree-group{color:var(--ink)}
.tree-group::before{color:var(--ink)}
.tree-word{color:var(--muted)}
.tree-word.active{color:var(--blue);text-decoration:underline}
.tree-root{left:16px;top:15px;font-size:10px;font-weight:500}
.go{width:10px;height:10px;border-radius:50%;background:#a4a8ad;left:276px}
.go.active{background:var(--blue)}
.go::after{content:"";position:absolute;left:3px;top:2.5px;border:2.5px solid transparent;border-left:4px solid #fff}
.help{display:inline-block;width:10px;height:10px;border-radius:50%;background:var(--ink);color:#fff;font-size:8px;text-align:center;line-height:10px;margin-left:3px;vertical-align:-1px}

.content{left:363px;top:96px;width:727px;height:1116px}
.title{left:0;width:727px;text-align:center;font-family:"Rubik",sans-serif;font-weight:600;color:var(--ink)}
.cta{left:222px;top:94px;width:298px;height:40px;background:var(--blue);border-radius:4px;color:#fff;font-size:13px;font-weight:700;text-align:center;line-height:40px}
.para{left:50px;width:640px;text-align:center;font-size:14px;line-height:22px;color:#333}
.step{width:46px;height:46px;border-radius:50%;top:289px;text-align:center;line-height:46px;font-family:"Rubik",sans-serif;font-weight:600;font-size:19px}
.step.done{background:var(--blue);color:#fff;box-shadow:0 0 0 4px #dbe5f5}
.step.todo{background:#fff;color:var(--blue);box-shadow:0 0 0 4px #eef2f8,0 2px 6px rgba(0,0,0,.08)}
.step-line{top:311px;height:2px}
.step-label{top:345px;width:100px;text-align:center;font-size:14px;font-weight:500}

.app-footer{left:0;top:1212px;width:1090px;height:80px;background:var(--footer);color:#fff;font-size:12px}
.copy{left:0;width:1090px;top:33px;text-align:center;padding-right:0}
.ver{left:1042px;top:35px;font-size:8px}

.overlay{left:0;top:0;width:1090px;height:1292px;background:rgba(0,0,0,.45)}
.modal{left:110px;top:94px;width:869px;height:323px;background:#fff;border-radius:16px}
.modal .select{border-color:#cfd3d7;color:#333}
.modal .select::after{border-top-color:var(--blue)}
.close{left:843px;top:15px;width:12px;height:12px;border-radius:50%;background:#b5b9bd}
.m-group{left:67px;font-size:13px;font-weight:500;color:var(--ink)}
.m-group::before{content:"";position:absolute;left:-14px;top:3px;border:4px solid transparent;border-left:5px solid var(--blue)}
.m-words{left:67px;font-size:13px;font-weight:500;color:#555;display:flex;white-space:nowrap}
.m-words span.sep{margin:0 24px;color:#777}
.m-active{color:var(--blue)}
</style>
</head>
<body>

<!-- Dashboard state -->
<div class="screen screen--main">
  <header class="abs app-header">
    <div class="abs brand">QUILLVANE</div>
    <div class="abs search"><svg width="10" height="10" viewBox="0 0 10 10"><circle cx="4" cy="4" r="3" fill="none" stroke="#333" stroke-width="1.5"/><line x1="6.3" y1="6.3" x2="9" y2="9" stroke="#333" stroke-width="1.5"/></svg>Search</div>
    <svg class="abs hdr-icon" style="left:838px" width="12" height="12" viewBox="0 0 12 12"><circle cx="6" cy="6" r="4" fill="none" stroke="#222" stroke-width="3" stroke-dasharray="2 1.2"/><circle cx="6" cy="6" r="1.5" fill="#222"/></svg>
    <svg class="abs hdr-icon" style="left:872px" width="12" height="13" viewBox="0 0 12 13"><path d="M6 1C3.5 1 3 3 3 5v3L1.5 10h9L9 8V5C9 3 8.5 1 6 1z" fill="#222"/><circle cx="6" cy="11.5" r="1.4" fill="#222"/></svg>
    <div class="abs user">DANA REYES ▾</div>
    <div class="abs avatar" role="img" aria-label="User avatar photo"></div>
    <div class="abs online"></div>
  </header>

  <aside class="abs sidebar">
    <div class="abs select" style="left:36px;top:38px;width:145px">All</div>
    <div class="abs expand-btn" style="top:38px">EXPAND</div>
    <div class="abs tree" style="top:85px">
      <div class="abs tree-root">WordNest Tutor</div>
      <div class="abs tree-item tree-group" style="left:31px;top:43px">Short-Term Memory<span class="help">?</span></div>
      <div class="abs tree-item tree-word active" style="left:47px;top:68px">Grab</div><div class="abs go active" style="top:69px"></div>
      <div class="abs tree-item tree-group" style="left:31px;top:96px">Working Memory<span class="help">?</span></div>
      <div class="abs tree-item tree-word" style="left:47px;top:121px">Cool Down</div><div class="abs go" style="top:122px"></div>
      <div class="abs tree-item tree-word" style="left:47px;top:145px">Crave</div><div class="abs go" style="top:146px"></div>
      <div class="abs tree-item tree-word" style="left:47px;top:170px">Go For</div><div class="abs go" style="top:171px"></div>
      <div class="abs tree-item tree-word" style="left:47px;top:195px">Go-To</div><div class="abs go" style="top:196px"></div>
      <div class="abs tree-item tree-word" style="left:47px;top:220px">In The Mood For</div><div class="abs go" style="top:221px"></div>
      <div class="abs tree-item tree-word" style="left:47px;top:244px">Sip Soothing</div><div class="abs go" style="top:245px"></div>
      <div class="abs tree-item tree-word" style="left:47px;top:269px">Stick With</div><div class="abs go" style="top:270px"></div>
      <div class="abs tree-item tree-word" style="left:47px;top:294px">Throw In/Throw On</div><div class="abs go" style="top:295px"></div>
      <div class="abs tree-item tree-group" style="left:31px;top:323px">Long-Term Memory<span class="help">?</span></div>
      <div class="abs tree-item tree-word" style="left:47px;top:348px">Give It A Try</div><div class="abs go" style="top:349px"></div>
    </div>
    <div class="abs select" style="left:36px;top:476px;width:298px">Daily English</div>
    <div class="abs select" style="left:36px;top:526px;width:298px">Business</div>
  </aside>

  <main class="abs content">
    <h1 class="abs title" style="top:42px;font-size:27px">GRAB</h1>
    <div class="abs cta">▸ START VOCABULARY REVIEW EXERCISE 3</div>
    <p class="abs para" style="top:155px">The word "grab" is most commonly used as a verb, meaning to take something quickly or suddenly. Imagine you're running late for school. You don't have time for breakfast, so you quickly grab an apple from the kitchen and rush out the door. As you reach the bus stop, your friend waves and says, "Hey! Let's grab a coffee after class." Later, when you sit down, your phone starts ringing. You grab it from your bag and answer.</p>
    <div class="abs step-line" style="left:210px;width:100px;background:var(--blue)"></div>
    <div class="abs step-line" style="left:333px;width:100px;background:var(--line)"></div>
    <div class="abs step-line" style="left:455px;width:100px;background:var(--line)"></div>
    <div class="abs step done" style="left:164px">1</div>
    <div class="abs step done" style="left:287px">2</div>
    <div class="abs step todo" style="left:410px">3</div>
    <div class="abs step todo" style="left:532px">4</div>
    <div class="abs step-label" style="left:137px">Review 1</div>
    <div class="abs step-label" style="left:260px">Review 2</div>
    <div class="abs step-label" style="left:383px">Review 3</div>
    <div class="abs step-label" style="left:505px">Review 4</div>
    <h2 class="abs title" style="top:414px;font-size:26px">LEARNING CURVE GRAPH</h2>
    <h2 class="abs title" style="top:891px;font-size:26px">WORDNEST TUTOR LEARNING ANALYSIS</h2>
    <p class="abs para" style="top:938px">Lorem ipsum dolor sit amet, consectetur adipiscing elit. Nam rutrum commodo enim id bibendum. Nunc dignissim risus erat, nec finibus nunc dictum eu. Aliquam sit amet euismod metus, quis malesuada erat. Sed at felis quis nulla feugiat cursus at at dolor. Maecenas pretium aliquet dapibus. Fusce et eleifend massa. Sed convallis ex mi, at lobortis ligula congue vel. Pellentesque pharetra molestie leo, sed vehicula felis commodo molestie. Aliquam dapibus ultrices efficitur. Duis porta mauris eros, at tempus sem tristique eget.</p>
  </main>

  <svg class="abs" style="left:415px;top:555px" width="640" height="380" viewBox="415 555 640 380" font-family="Roboto, sans-serif" font-size="11" font-weight="700">
    <rect x="500" y="569" width="538" height="338" fill="none" stroke="#dcdfe3"/>
    <g stroke="#e4e6e9"><line x1="577" y1="569" x2="577" y2="907"/><line x1="654" y1="569" x2="654" y2="907"/><line x1="730" y1="569" x2="730" y2="907"/><line x1="807" y1="569" x2="807" y2="907"/><line x1="883" y1="569" x2="883" y2="907"/><line x1="960" y1="569" x2="960" y2="907"/></g>
    <g text-anchor="end" fill="#2b2f33"><text x="489" y="573">$3,500,000</text><text x="489" y="619">$3,000,000</text><text x="489" y="677">$2,500,000</text><text x="489" y="734">$1,500,000</text><text x="489" y="792">$1,000,000</text><text x="489" y="838">$500,000</text><text x="489" y="896">$0</text></g>
    <g fill="#2b333d"><rect x="520" y="626" width="14" height="280"/><rect x="597" y="654" width="14" height="252"/><rect x="673" y="766" width="14" height="140"/><rect x="749" y="626" width="14" height="280"/><rect x="826" y="626" width="14" height="280"/><rect x="898" y="738" width="14" height="168"/><rect x="972" y="766" width="14" height="140"/></g>
    <g fill="#2d64b5"><rect x="543" y="654" width="14" height="252"/><rect x="620" y="682" width="14" height="224"/><rect x="696" y="626" width="14" height="280"/><rect x="772" y="738" width="14" height="168"/><rect x="849" y="654" width="14" height="252"/><rect x="921" y="696" width="14" height="210"/><rect x="995" y="626" width="14" height="280"/></g>
    <g text-anchor="middle" fill="#2b2f33" font-size="10.5">
      <text x="527" y="617">100</text><text x="550" y="645">90</text><text x="604" y="645">90</text><text x="627" y="673">80</text>
      <text x="680" y="757">50</text><text x="703" y="617">100</text><text x="756" y="617">100</text><text x="779" y="729">60</text>
      <text x="833" y="617">100</text><text x="856" y="645">90</text><text x="905" y="729">60</text><text x="928" y="687">75</text>
      <text x="979" y="757">50</text><text x="1002" y="617">100</text>
    </g>
    <g text-anchor="middle" fill="#2b2f33" font-size="12" font-weight="500"><text x="539" y="927">Sun</text><text x="616" y="927">Mon</text><text x="692" y="927">Tue</text><text x="768" y="927">Wed</text><text x="845" y="927">Thu</text><text x="917" y="927">Fri</text><text x="991" y="927">Sat</text></g>
  </svg>

  <footer class="abs app-footer">
    <div class="abs copy">© 2025 <b>QuillVane</b> &nbsp;|&nbsp; All Rights Reserved</div>
    <div class="abs ver">C45</div>
  </footer>
</div>

<!-- Expanded vocabulary state -->
<div class="screen screen--expanded">
  <header class="abs app-header">
    <div class="abs brand">QUILLVANE</div>
    <div class="abs search"><svg width="10" height="10" viewBox="0 0 10 10"><circle cx="4" cy="4" r="3" fill="none" stroke="#333" stroke-width="1.5"/><line x1="6.3" y1="6.3" x2="9" y2="9" stroke="#333" stroke-width="1.5"/></svg>Search</div>
    <svg class="abs hdr-icon" style="left:838px" width="12" height="12" viewBox="0 0 12 12"><circle cx="6" cy="6" r="4" fill="none" stroke="#222" stroke-width="3" stroke-dasharray="2 1.2"/><circle cx="6" cy="6" r="1.5" fill="#222"/></svg>
    <svg class="abs hdr-icon" style="left:872px" width="12" height="13" viewBox="0 0 12 13"><path d="M6 1C3.5 1 3 3 3 5v3L1.5 10h9L9 8V5C9 3 8.5 1 6 1z" fill="#222"/><circle cx="6" cy="11.5" r="1.4" fill="#222"/></svg>
    <div class="abs user">DANA REYES ▾</div>
    <div class="abs avatar" role="img" aria-label="User avatar photo"></div>
    <div class="abs online"></div>
  </header>

  <aside class="abs sidebar">
    <div class="abs select" style="left:36px;top:38px;width:145px">All</div>
    <div class="abs expand-btn" style="top:38px">EXPAND</div>
    <div class="abs tree" style="top:85px">
      <div class="abs tree-root">WordNest Tutor</div>
      <div class="abs tree-item tree-group" style="left:31px;top:43px">Short-Term Memory<span class="help">?</span></div>
      <div class="abs tree-item tree-word active" style="left:47px;top:68px">Grab</div><div class="abs go active" style="top:69px"></div>
      <div class="abs tree-item tree-group" style="left:31px;top:96px">Working Memory<span class="help">?</span></div>
      <div class="abs tree-item tree-word" style="left:47px;top:121px">Cool Down</div><div class="abs go" style="top:122px"></div>
      <div class="abs tree-item tree-word" style="left:47px;top:145px">Crave</div><div class="abs go" style="top:146px"></div>
      <div class="abs tree-item tree-word" style="left:47px;top:170px">Go For</div><div class="abs go" style="top:171px"></div>
      <div class="abs tree-item tree-word" style="left:47px;top:195px">Go-To</div><div class="abs go" style="top:196px"></div>
      <div class="abs tree-item tree-word" style="left:47px;top:220px">In The Mood For</div><div class="abs go" style="top:221px"></div>
      <div class="abs tree-item tree-word" style="left:47px;top:244px">Sip Soothing</div><div class="abs go" style="top:245px"></div>
      <div class="abs tree-item tree-word" style="left:47px;top:269px">Stick With</div><div class="abs go" style="top:270px"></div>
      <div class="abs tree-item tree-word" style="left:47px;top:294px">Throw In/Throw On</div><div class="abs go" style="top:295px"></div>
      <div class="abs tree-item tree-group" style="left:31px;top:323px">Long-Term Memory<span class="help">?</span></div>
      <div class="abs tree-item tree-word" style="left:47px;top:348px">Give It A Try</div><div class="abs go" style="top:349px"></div>
    </div>
    <div class="abs select" style="left:36px;top:476px;width:298px">Daily English</div>
    <div class="abs select" style="left:36px;top:526px;width:298px">Business</div>
  </aside>

  <main class="abs content">
    <h1 class="abs title" style="top:42px;font-size:27px">GRAB</h1>
    <div class="abs cta">▸ START VOCABULARY REVIEW EXERCISE 3</div>
    <p class="abs para" style="top:155px">The word "grab" is most commonly used as a verb, meaning to take something quickly or suddenly. Imagine you're running late for school. You don't have time for breakfast, so you quickly grab an apple from the kitchen and rush out the door. As you reach the bus stop, your friend waves and says, "Hey! Let's grab a coffee after class." Later, when you sit down, your phone starts ringing. You grab it from your bag and answer.</p>
    <div class="abs step-line" style="left:210px;width:100px;background:var(--blue)"></div>
    <div class="abs step-line" style="left:333px;width:100px;background:var(--line)"></div>
    <div class="abs step-line" style="left:455px;width:100px;background:var(--line)"></div>
    <div class="abs step done" style="left:164px">1</div>
    <div class="abs step done" style="left:287px">2</div>
    <div class="abs step todo" style="left:410px">3</div>
    <div class="abs step todo" style="left:532px">4</div>
    <div class="abs step-label" style="left:137px">Review 1</div>
    <div class="abs step-label" style="left:260px">Review 2</div>
    <div class="abs step-label" style="left:383px">Review 3</div>
    <div class="abs step-label" style="left:505px">Review 4</div>
    <h2 class="abs title" style="top:414px;font-size:26px">LEARNING CURVE GRAPH</h2>
    <h2 class="abs title" style="top:891px;font-size:26px">WORDNEST TUTOR LEARNING ANALYSIS</h2>
    <p class="abs para" style="top:938px">Lorem ipsum dolor sit amet, consectetur adipiscing elit. Nam rutrum commodo enim id bibendum. Nunc dignissim risus erat, nec finibus nunc dictum eu. Aliquam sit amet euismod metus, quis malesuada erat. Sed at felis quis nulla feugiat cursus at at dolor. Maecenas pretium aliquet dapibus. Fusce et eleifend massa. Sed convallis ex mi, at lobortis ligula congue vel. Pellentesque pharetra molestie leo, sed vehicula felis commodo molestie. Aliquam dapibus ultrices efficitur. Duis porta mauris eros, at tempus sem tristique eget.</p>
  </main>

  <svg class="abs" style="left:415px;top:555px" width="640" height="380" viewBox="415 555 640 380" font-family="Roboto, sans-serif" font-size="11" font-weight="700">
    <rect x="500" y="569" width="538" height="338" fill="none" stroke="#dcdfe3"/>
    <g stroke="#e4e6e9"><line x1="577" y1="569" x2="577" y2="907"/><line x1="654" y1="569" x2="654" y2="907"/><line x1="730" y1="569" x2="730" y2="907"/><line x1="807" y1="569" x2="807" y2="907"/><line x1="883" y1="569" x2="883" y2="907"/><line x1="960" y1="569" x2="960" y2="907"/></g>
    <g text-anchor="end" fill="#2b2f33"><text x="489" y="573">$3,500,000</text><text x="489" y="619">$3,000,000</text><text x="489" y="677">$2,500,000</text><text x="489" y="734">$1,500,000</text><text x="489" y="792">$1,000,000</text><text x="489" y="838">$500,000</text><text x="489" y="896">$0</text></g>
    <g fill="#2b333d"><rect x="520" y="626" width="14" height="280"/><rect x="597" y="654" width="14" height="252"/><rect x="673" y="766" width="14" height="140"/><rect x="749" y="626" width="14" height="280"/><rect x="826" y="626" width="14" height="280"/><rect x="898" y="738" width="14" height="168"/><rect x="972" y="766" width="14" height="140"/></g>
    <g fill="#2d64b5"><rect x="543" y="654" width="14" height="252"/><rect x="620" y="682" width="14" height="224"/><rect x="696" y="626" width="14" height="280"/><rect x="772" y="738" width="14" height="168"/><rect x="849" y="654" width="14" height="252"/><rect x="921" y="696" width="14" height="210"/><rect x="995" y="626" width="14" height="280"/></g>
    <g text-anchor="middle" fill="#2b2f33" font-size="10.5">
      <text x="527" y="617">100</text><text x="550" y="645">90</text><text x="604" y="645">90</text><text x="627" y="673">80</text>
      <text x="680" y="757">50</text><text x="703" y="617">100</text><text x="756" y="617">100</text><text x="779" y="729">60</text>
      <text x="833" y="617">100</text><text x="856" y="645">90</text><text x="905" y="729">60</text><text x="928" y="687">75</text>
      <text x="979" y="757">50</text><text x="1002" y="617">100</text>
    </g>
    <g text-anchor="middle" fill="#2b2f33" font-size="12" font-weight="500"><text x="539" y="927">Sun</text><text x="616" y="927">Mon</text><text x="692" y="927">Tue</text><text x="768" y="927">Wed</text><text x="845" y="927">Thu</text><text x="917" y="927">Fri</text><text x="991" y="927">Sat</text></g>
  </svg>

  <footer class="abs app-footer">
    <div class="abs copy">© 2025 <b>QuillVane</b> &nbsp;|&nbsp; All Rights Reserved</div>
    <div class="abs ver">C45</div>
  </footer>

  <div class="abs overlay"></div>
  <section class="abs modal" aria-label="All vocabulary">
    <div class="abs close"></div>
    <div class="abs select" style="left:52px;top:42px;width:145px">All</div>
    <div class="abs m-group" style="top:108px">Short-Term Memory</div>
    <div class="abs m-words" style="top:134px"><span class="m-active">Grab</span></div>
    <div class="abs m-group" style="top:162px">Working Memory</div>
    <div class="abs m-words" style="top:188px"><span>Cool Down</span><span class="sep">/</span><span>Crave</span><span class="sep">/</span><span>Go For</span><span class="sep">/</span><span>Go-To</span><span class="sep">/</span><span>In The Mood For</span><span class="sep">/</span><span>Sip</span><span class="sep">/</span><span>Soothing</span><span class="sep">/</span><span>Stick With</span></div>
    <div class="abs m-words" style="top:209px"><span>Throw In/Throw On</span></div>
    <div class="abs m-group" style="top:239px">Long-Term Memory</div>
    <div class="abs m-words" style="top:265px"><span>Give It A Try</span></div>
  </section>
</div>

</body>
</html>
```